Small Business Broker Business Card Design

A business card design for a small business brokerage, which is a financial service, not unlike real estate brokerage, but for small businesses such as laundromats, pizza shops, restaurants, cleaners etc. The designs should all be simple, more conservative in nature, using the colors and font of the logo. Again, think real estate Brokerage as a business context
Contact Information for Business Card
Name: Glen R. Harlow. Title: Small Business Advisor. Email: g.harlow@bayfieldcapitalworks.example. Mobile: (555) 274-3918. Office: (555) 806-2147. www.bayfieldcapitalworks.example

```html
<!DOCTYPE html>
<html lang="en">
<head>
<meta charset="utf-8">
<title>Bayfield Capital Works – Business Card</title>
<link rel="stylesheet" href="https://fonts.googleapis.com/css2?family=Montserrat:wght@600;700&family=Open+Sans:wght@400&display=swap">
<style>
  :root {
    --stage: #232323;
    --card: #1b1c1e;
    --green: #8dc63f;
    --blue: #1f4583;
    --ink: #ffffff;
    --pattern-light: #6f6f6f;
    --pattern-dark: #0b0b0b;
  }
  * { box-sizing: border-box; margin: 0; padding: 0; }
  html, body { width: 1200px; height: 780px; overflow: hidden; }
  body {
    background: var(--stage);
    display: flex;
    align-items: center;
    justify-content: center;
    gap: 40px;
  }
  .card {
    position: relative;
    width: 540px;
    height: 309px;
    border-radius: 22px;
    border: 3px solid var(--green);
    overflow: hidden;
    background: var(--card);
  }

  /* Back side */
  .card-back .pattern {
    position: absolute;
    inset: 0;
    background: linear-gradient(120deg, var(--pattern-light) 0%, #3a3a3a 40%, var(--pattern-dark) 75%);
  }
  .card-back .brand-mark {
    position: absolute;
    inset: 0;
    display: flex;
    align-items: center;
    justify-content: center;
    gap: 8px;
  }
  .brand-square { width: 12px; height: 12px; background: var(--green); }
  .brand-name {
    font-family: "Montserrat", sans-serif;
    font-weight: 700;
    font-size: 15px;
    letter-spacing: 1px;
    color: var(--blue);
    text-transform: uppercase;
  }

  /* Front side */
  .company {
    position: absolute;
    top: 62px;
    right: 38px;
    text-align: right;
  }
  .company .brand-name { font-size: 18px; }
  .tagline {
    margin-top: 4px;
    font-family: "Montserrat", sans-serif;
    font-weight: 600;
    font-size: 8px;
    letter-spacing: 1px;
    color: var(--green);
    text-transform: uppercase;
  }
  .identity {
    position: absolute;
    left: 0;
    top: 150px;
    padding-left: 34px;
    border-left: 14px solid var(--green);
  }
  .person-name {
    font-family: "Montserrat", sans-serif;
    font-weight: 700;
    font-size: 24px;
    letter-spacing: 1px;
    color: var(--blue);
    text-transform: uppercase;
    line-height: 1.1;
  }
  .person-title {
    font-family: "Open Sans", sans-serif;
    font-size: 15px;
    color: var(--green);
  }
  .contact-list {
    position: absolute;
    left: 48px;
    top: 222px;
    list-style: none;
    font-family: "Open Sans", sans-serif;
    font-size: 13px;
    color: var(--ink);
    line-height: 18px;
  }
  .contact-list li { display: flex; align-items: center; gap: 7px; }
  .contact-list svg { width: 11px; height: 11px; fill: none; stroke: var(--green); stroke-width: 1.6; flex: none; }
</style>
</head>
<body>

<section class="card card-back" aria-label="Card back">
  <div class="pattern" role="img" aria-label="Decorative chevron pattern in grey to black"></div>
  <div class="brand-mark">
    <span class="brand-square"></span>
    <span class="brand-name">Bayfield Capital Works</span>
  </div>
</section>

<section class="card card-front" aria-label="Card front">
  <div class="company">
    <p class="brand-name">Bayfield Capital Works, Inc</p>
    <p class="tagline">Confidently buy or sell a local business today</p>
  </div>

  <div class="identity">
    <h1 class="person-name">Glen R. Harlow</h1>
    <p class="person-title">Small Business Advisor</p>
  </div>

  <ul class="contact-list">
    <li>
      <svg viewBox="0 0 12 12" aria-hidden="true"><rect x="3" y="1" width="6" height="10" rx="1"/></svg>
      (555) 274-3918
    </li>
    <li>
      <svg viewBox="0 0 12 12" aria-hidden="true"><path d="M1 5 Q6 1 11 5 L9 6 L8 4 H4 L3 6 Z M3 7 H9 V11 H3 Z"/></svg>
      (555) 806-2147
    </li>
    <li>
      <svg viewBox="0 0 12 12" aria-hidden="true"><rect x="1" y="3" width="10" height="7"/><path d="M1 3 L6 7 L11 3"/></svg>
      g.harlow@bayfieldcapitalworks.example
    </li>
    <li>
      <svg viewBox="0 0 12 12" aria-hidden="true"><circle cx="6" cy="6" r="5"/><path d="M1 6 H11 M6 1 Q3 6 6 11 Q9 6 6 1"/></svg>
      www.bayfieldcapitalworks.example
    </li>
  </ul>
</section>

</body>
</html>
```